Business card for acupunctist in Melbourne. Specialises in Fertility, pre and post natal care, pain

I am looking for a business card which is going to catch people eyes. Two sided, one side in a muted colour (keeping it feminine) (pink or yellow???)maybe with a little simple logo or picture, the other side I was thinking white with 3 colours (pink grey and yellow... Had these in mind.
Info on the card
Mirren Costa Acupuncture

Dr Mirren Costa (TCM Acupuncture)
Acupuncture for balancing body and mind.
Willowmere Therapeutics
14 Ferndale Road, Oakhurst 3071.
94726151
0428319574
Mirrentcm@quillpost.net

Some other little logo/ designs I have liked are as follows:
http://www.dorotheabrisklac.net/rates-and-insurance/
http://www.rosalindpeverell.net/
http://www.tz-acupuncture.example.uk/

Target Market(s)

professional women, people in pain, active people, people seeking a healthy lifefstyle.

Industry/Entity Type

Business

Font styles to use
Serif
Sans Serif

Colors
eea4c8
fde08a
aaaaaa

Requirements
Must have
• Must be eye catching, but not too loud and busy. Subltle is good. Simple is also good. The logo could be something that represents growth and health and nurturing. Again not too elaborate, very simple.
Thankyou
Should not have
• Electric colours, crazy fonts, Pictures of yin and yang, candles, or bodies.

```html
<!DOCTYPE html>
<html lang="en">
<head>
<meta charset="utf-8">
<title>Mirren Costa Acupuncture – Business Card</title>
<link rel="stylesheet" href="https://fonts.googleapis.com/css2?family=Open+Sans:wdth,wght@75..100,400..800&display=swap">
<style>
  :root {
    --stage: #ececec;
    --charcoal: #2f2f31;
    --blush: #e8b2b0;
    --rose: #d9718f;
    --sun: #f5e214;
    --lime-gold: #e6e14a;
    --stripe-grey: #a9a9a9;
    --stripe-white: #f4f4f4;
    --ink: #111111;
    --paper: #ffffff;
  }
  * { box-sizing: border-box; margin: 0; padding: 0; }
  html, body { width: 1200px; height: 900px; overflow: hidden; }
  body {
    background: var(--stage);
    font-family: "Open Sans", Arial, sans-serif;
    display: flex;
    flex-direction: column;
    align-items: center;
    justify-content: center;
    gap: 56px;
  }
  .card {
    position: relative;
    width: 640px;
    height: 366px;
    overflow: hidden;
    box-shadow: 0 6px 18px rgba(0,0,0,.18);
  }

  /* ---------- contact side ---------- */
  .card--contact { background: var(--charcoal); color: var(--paper); }
  .brand {
    position: absolute; left: 44px; top: 40px;
    display: flex; align-items: center; gap: 12px;
  }
  .brand__dot {
    width: 18px; height: 18px; border-radius: 50%;
    background: var(--rose);
  }
  .brand__name {
    font-stretch: 78%; font-weight: 800; font-size: 30px;
    text-transform: uppercase; letter-spacing: -0.5px;
    color: var(--rose);
  }
  .brand__sub {
    position: absolute; left: 74px; top: 84px;
    font-size: 12px; color: #d8d8d8;
  }
  .practitioner {
    position: absolute; right: 40px; top: 36px; text-align: right;
  }
  .practitioner__name {
    font-stretch: 85%; font-weight: 800; font-size: 20px;
    text-transform: uppercase;
  }
  .practitioner__title { font-size: 12px; color: var(--lime-gold); }
  .contact-list {
    position: absolute; list-style: none; font-size: 12px; color: #ececec;
  }
  .contact-list li { display: flex; align-items: center; gap: 9px; margin-bottom: 8px; }
  .contact-list svg { width: 12px; height: 12px; flex: none; }
  .contact-list--left { left: 44px; top: 128px; }
  .contact-list--right { left: 390px; top: 212px; }

  .band { position: absolute; left: 0; right: 0; }
  .band--white { height: 5px; background: var(--stripe-white); }
  .band--grey { height: 7px; background: repeating-linear-gradient(90deg, var(--stripe-grey) 0 2px, #c4c4c4 2px 4px); }
  .card--contact .band--white.top { top: 276px; }
  .card--contact .band--grey { top: 281px; }
  .band--rose { top: 288px; height: 44px; background: var(--rose); }
  .card--contact .band--white.bottom { top: 332px; }

  /* ---------- brand side ---------- */
  .card--brand { background: var(--blush); color: var(--ink); }
  .emblem {
    position: absolute; left: 50%; top: 118px; transform: translateX(-50%);
    display: flex; flex-direction: column; align-items: center; gap: 8px;
  }
  .emblem__dot {
    width: 22px; height: 22px; border-radius: 50%; background: var(--rose);
  }
  .emblem__name {
    font-stretch: 78%; font-weight: 800; font-size: 40px;
    text-transform: uppercase; letter-spacing: -1px; white-space: nowrap;
  }
  .emblem__tagline { font-size: 14px; margin-top: -8px; }
  .card--brand .band--white { top: 276px; }
  .card--brand .band--grey { top: 281px; }
  .card--brand .band--white.lower { top: 288px; }
  .band--sun { top: 293px; bottom: 0; background: var(--sun); }
</style>
</head>
<body>

  <section class="card card--contact" aria-label="Contact side">
    <div class="brand">
      <span class="brand__dot"></span>
      <span class="brand__name">Mirren Costa Acupuncture</span>
    </div>
    <p class="brand__sub">Willowmere Therapeutics</p>

    <div class="practitioner">
      <p class="practitioner__name">Dr Mirren Costa</p>
      <p class="practitioner__title">TCM Acupuncture</p>
    </div>

    <ul class="contact-list contact-list--left">
      <li>
        <svg viewBox="0 0 12 12"><path d="M6 0.5a4 4 0 0 0-4 4c0 3 4 7 4 7s4-4 4-7a4 4 0 0 0-4-4zm0 5.5a1.5 1.5 0 1 1 0-3 1.5 1.5 0 0 1 0 3z" fill="#e6e14a"/></svg>
        14 Ferndale Road, Oakhurst 3071.
      </li>
      <li>
        <svg viewBox="0 0 12 12"><rect x="0.75" y="2.25" width="10.5" height="7.5" fill="none" stroke="#e6e14a" stroke-width="1.2"/><path d="M1 2.5l5 4 5-4" fill="none" stroke="#e6e14a" stroke-width="1.2"/></svg>
        Mirrentcm@quillpost.net
      </li>
    </ul>

    <ul class="contact-list contact-list--right">
      <li>
        <svg viewBox="0 0 12 12"><path d="M3 1l2 2.5-1.2 1.3a7 7 0 0 0 3.4 3.4L8.5 7 11 9l-1.5 2C5 10.5 1.5 7 1 2.5z" fill="#e6e14a"/></svg>
        94726151
      </li>
      <li>
        <svg viewBox="0 0 12 12"><rect x="3" y="0.75" width="6" height="10.5" rx="1" fill="none" stroke="#e6e14a" stroke-width="1.2"/></svg>
        0428319574
      </li>
    </ul>

    <div class="band band--white top"></div>
    <div class="band band--grey"></div>
    <div class="band band--rose"></div>
    <div class="band band--white bottom"></div>
  </section>

  <section class="card card--brand" aria-label="Brand side">
    <div class="emblem">
      <span class="emblem__dot"></span>
      <h1 class="emblem__name">Mirren Costa Acupuncture</h1>
      <p class="emblem__tagline">Acupuncture for balancing body and mind</p>
    </div>

    <div class="band band--white"></div>
    <div class="band band--grey"></div>
    <div class="band band--white lower"></div>
    <div class="band band--sun"></div>
  </section>

</body>
</html>
```